Appraisal and Umpire Services for Property Damage Insurance Claims

I need a banner design that I can post as an advertisement on industry web pages. I would like this to be elegant and reflective of quality, integrity and professionalism.

Target Market(s)

Insurance Companies and Attorneys

Industry/Entity Type

Insurance

Contact Information for Business Card

Gordon T. Ashby
218 Birchwell Lane
PO Box 913
Clifton Park, NY 12348
gashby@meridaleclaims.com
Phone: (800) 519-4867, Ext. 2716
Direct: (315) 648-9052

Logo Text

Line One: Silver Hollow Claim Service, Inc. Line two: Appraisal and Umpire Services

Font styles to use
Serif
Sans Serif

Colors
0255a3
f78f20
faa54b
3176b5

Requirements
Must have
• New Logo and matching banner, business card and stationary.
• The colors must be orange and navy blue in the logo. I have selected them below.

```html
<!DOCTYPE html>
<html lang="en">
<head>
<meta charset="utf-8">
<title>Silver Hollow Claim Service, Inc — Stationery</title>
<link rel="stylesheet" href="https://fonts.googleapis.com/css2?family=Source+Sans+3:wght@400;600&display=swap">
<style>
  :root {
    --navy: #0255a3;
    --navy-light: #3176b5;
    --orange: #f78f20;
    --backdrop: #e2e2e2;
    --paper: #ffffff;
    --paper-shadow: rgba(0, 0, 0, 0.14);
  }
  * { box-sizing: border-box; margin: 0; padding: 0; }
  html, body { width: 1200px; height: 640px; overflow: hidden; }
  body {
    background: var(--backdrop);
    font-family: "Source Sans 3", "Myriad Pro", Arial, sans-serif;
    position: relative;
  }
  .sheet {
    position: absolute;
    background: var(--paper);
    box-shadow: 0 2px 8px var(--paper-shadow);
  }
  .letterhead-second { left: 40px; top: 110px; width: 292px; height: 416px; }
  .letterhead-first { left: 280px; top: 156px; width: 292px; height: 416px; }
  .envelope { left: 592px; top: 46px; width: 328px; height: 128px; }
  .business-card { left: 682px; top: 312px; width: 270px; height: 155px; }

  .brand {
    position: absolute;
    display: flex;
    align-items: center;
    gap: 3px;
    white-space: nowrap;
  }
  .brand-dot { flex: none; display: block; }
  .brand-dot circle { fill: var(--orange); }
  .brand-name {
    color: var(--navy);
    font-weight: 400;
    line-height: 0.95;
  }

  .letterhead-second .brand { left: 22px; bottom: 30px; }
  .letterhead-first .brand { right: 26px; top: 16px; }
  .envelope .brand { left: 20px; bottom: 16px; }
  .letterhead-second .brand-name,
  .letterhead-first .brand-name,
  .envelope .brand-name { font-size: 8.5px; }

  .business-card .brand { left: 26px; top: 24px; gap: 6px; }
  .business-card .brand-name { font-size: 14.5px; }

  .contact-block {
    position: absolute;
    color: var(--navy-light);
  }
  .contact-block .contact-label { color: var(--navy); font-weight: 600; }
  .letterhead-first .contact-block { left: 24px; bottom: 20px; font-size: 4.5px; line-height: 1.05; }
  .business-card .contact-block { left: 29px; top: 103px; font-size: 9.5px; line-height: 1; }
</style>
</head>
<body>
  <section class="sheet letterhead-second" aria-label="Letterhead, continuation sheet">
    <div class="brand">
      <svg class="brand-dot" width="19" height="19" viewBox="0 0 20 20" aria-hidden="true"><circle cx="10" cy="10" r="10"/></svg>
      <span class="brand-name">Silver Hollow<br>Claim Service, Inc</span>
    </div>
  </section>

  <section class="sheet letterhead-first" aria-label="Letterhead, first sheet">
    <div class="brand">
      <svg class="brand-dot" width="19" height="19" viewBox="0 0 20 20" aria-hidden="true"><circle cx="10" cy="10" r="10"/></svg>
      <span class="brand-name">Silver Hollow<br>Claim Service, Inc</span>
    </div>
    <div class="contact-block">
      <p class="contact-label">Contact</p>
      <p>Gordon T. Ashby</p>
      <p>Email: gashby@meridaleclaims.com</p>
      <p>Phone: (800) 519-4867, Ext. 2716</p>
    </div>
  </section>

  <section class="sheet envelope" aria-label="Envelope">
    <div class="brand">
      <svg class="brand-dot" width="19" height="19" viewBox="0 0 20 20" aria-hidden="true"><circle cx="10" cy="10" r="10"/></svg>
      <span class="brand-name">Silver Hollow<br>Claim Service, Inc</span>
    </div>
  </section>

  <section class="sheet business-card" aria-label="Business card">
    <div class="brand">
      <svg class="brand-dot" width="36" height="36" viewBox="0 0 20 20" aria-hidden="true"><circle cx="10" cy="10" r="10"/></svg>
      <span class="brand-name">Silver Hollow<br>Claim Service, Inc</span>
    </div>
    <div class="contact-block">
      <p class="contact-label">Contact</p>
      <p>Gordon T. Ashby</p>
      <p>Email: gashby@meridaleclaims.com</p>
      <p>Phone: (800) 519-4867, Ext. 2716</p>
    </div>
  </section>
</body>
</html>
```